Sell the dream! Property investment proposal document

We are looking for a proposal document which outlines our vision for property development. The purpose of the document is to raise investment from investors - sell the dream!
Brief summary:
Kestrel Dwellings Developments, is an emerging New Zealand property investment company with a focus on providing unique property investment opportunities.
Our expertise and capabilities in architectural modular homes provide us with a remarkable advantage in tackling the development of properties that are typically considered challenging, remote, or uniquely positioned.
Our specialization in this niche sector of property development not only sets us apart from competitors, but also paves the way for lucrative investment opportunities in the New Zealand property market.
Feel free to use any images from www.kestreldwellings.co.nz
Target Market(s)
investors for a unique property development opportunity
Industry/Entity Type
luxury property development in unique locations throughout New Zealand
Colors
Designer to choose only greyscale colors for use in the design.
Look and feel

```html
<!DOCTYPE html>
<html lang="en">
<head>
<meta charset="utf-8">
<title>Kestrel – Sell the dream! Property investment proposal</title>
<link href="https://fonts.googleapis.com/css2?family=Montserrat:wght@200;300;400;500;600;700&display=swap" rel="stylesheet">
<style>
:root{
  --stage-top:#3b3b3b;
  --stage:#333333;
  --black:#050505;
  --ink:#0d0d0e;
  --charcoal:#131315;
  --band:#1b1b1d;
  --slate:#1e1e20;
  --white:#ffffff;
  --rule:#3f3f42;
  --muted:#8a8a8c;
  --title-grey:#7e7d76;
  --label:#bdbdbd;
  --faint:#d9d9d9;
}
*{box-sizing:border-box;margin:0;padding:0}
html,body{width:1200px;height:2397px;overflow:hidden}
body{background:var(--stage);font-family:"Montserrat",sans-serif;position:relative;color:var(--white)}
.hero{position:absolute;left:0;top:0;width:1200px;height:675px;background:var(--stage-top)}
.hero-title{position:absolute;left:92px;top:40px;font-size:118px;font-weight:400;letter-spacing:-5px;color:var(--title-grey);line-height:1}
.hero-caption{position:absolute;left:744px;top:528px;color:#d4d4d4;font-weight:300}
.hero-caption .main{font-size:29px;line-height:1.1}
.hero-caption .sub{font-size:19px;line-height:1.3}
.hero-preview{position:absolute;left:224px;top:214px;width:1004px;height:354px;transform:scale(.75);transform-origin:0 0;box-shadow:0 20px 40px rgba(0,0,0,.45)}

.label{position:absolute;width:500px;text-align:center;font-size:22px;font-weight:300;color:var(--label)}
.spread{position:absolute;left:98px;width:1004px;height:354px}
.page{position:absolute;top:0;width:500px;height:354px;overflow:hidden;background:var(--black)}
.page.left{left:0}
.page.right{left:504px}
.block{position:absolute}
.photo{position:absolute}
.hrule{position:absolute;height:1px;background:var(--rule)}
.vrule{position:absolute;width:1px;background:var(--rule)}

.url{position:absolute;font-size:7px;letter-spacing:4.2px;color:var(--muted);white-space:nowrap;transform:rotate(-90deg);transform-origin:0 0;font-weight:300}
.contact{position:absolute;font-size:5.6px;line-height:1.35;color:var(--muted);font-weight:300}
.tagline{position:absolute;font-size:5.6px;line-height:1.3;color:var(--muted);font-weight:300}
.tagline.dark{color:#777}
.brand-faint{position:absolute;font-weight:500;letter-spacing:-2px;line-height:1;white-space:nowrap}
.body-copy{position:absolute;font-size:5px;line-height:1.38;font-weight:300}
.body-copy p{margin-bottom:4px}
.body-copy.on-light{color:#333}
.body-copy.on-dark{color:#bdbdbd}
.heading{position:absolute;font-weight:600;font-size:24px;line-height:.98}
.heading.dark{color:#111}
.cover-line{position:absolute;left:28px;top:24px;font-size:26px;font-weight:200;color:var(--white);letter-spacing:.3px}
.cover-name{position:absolute;left:110px;top:236px;font-size:86px;font-weight:500;letter-spacing:-3px;color:var(--white);line-height:1}
.vertical-title{position:absolute;left:30px;top:205px;transform:rotate(-90deg);transform-origin:0 0;font-size:24px;font-weight:600;line-height:.98;color:var(--white);white-space:nowrap}
</style>
</head>
<body>

<section class="hero">
  <div class="hero-title">Kestrel</div>

  <div class="hero-preview">
    <div class="page left cover-back">
      <div class="block" style="left:0;top:0;width:441px;height:75px;background:var(--black)"></div>
      <div class="block" style="left:441px;top:0;width:59px;height:75px;background:var(--charcoal)"></div>
      <div class="block" style="left:0;top:75px;width:441px;height:201px;background:var(--ink)"></div>
      <div class="photo" role="img" aria-label="Lake at dusk with forest shoreline" style="left:441px;top:75px;width:59px;height:201px;background:linear-gradient(180deg,#c9b79a 0%,#8a7a62 45%,#3e3a32 100%)"></div>
      <div class="hrule" style="left:0;top:75px;width:500px"></div>
      <div class="hrule" style="left:0;top:276px;width:500px"></div>
      <div class="block" style="left:0;top:276px;width:500px;height:78px;background:var(--band)"></div>
      <div class="brand-faint" style="left:112px;top:130px;font-size:82px;color:#3a3a3c">Kestrel</div>
      <div class="url" style="left:25px;top:262px">www.kestreldwellings.co.nz</div>
      <div class="contact" style="left:45px;top:320px">09 555 0142<br>sales@kestreldwellings.co.nz</div>
    </div>
    <div class="page right cover-front">
      <div class="block" style="left:0;top:0;width:500px;height:75px;background:var(--charcoal)"></div>
      <div class="cover-line">Sell the dream!</div>
      <div class="block" style="left:358px;top:75px;width:142px;height:102px;background:var(--slate)"></div>
      <div class="photo" role="img" aria-label="Timber modular cabin with lit windows on a rocky lakeshore among pines" style="left:0;top:75px;width:358px;height:201px;background:linear-gradient(160deg,#7d7566 0%,#4a4034 40%,#2b2520 75%,#171513 100%)"></div>
      <div class="block" style="left:0;top:276px;width:87px;height:78px;background:var(--band)"></div>
      <div class="vrule" style="left:358px;top:0;height:177px"></div>
      <div class="hrule" style="left:0;top:75px;width:358px"></div>
      <div class="brand-faint" style="left:398px;top:24px;font-size:22px;letter-spacing:0;color:#6a6a6c">Kestrel</div>
      <div class="url" style="left:478px;top:262px">www.kestreldwellings.co.nz</div>
      <div class="tagline" style="left:28px;top:310px">Modular<br>Architectural<br>Homes</div>
      <div class="cover-name">Kestrel</div>
    </div>
  </div>

  <div class="hero-caption">
    <div class="main">Sell the dream!</div>
    <div class="sub">Property investment proposal document</div>
  </div>
</section>

<!-- Cover spread -->
<div class="label" style="left:98px;top:712px">Back</div>
<div class="label" style="left:602px;top:712px">Front</div>
<div class="spread" style="top:752px">
  <div class="page left cover-back">
    <div class="block" style="left:0;top:0;width:441px;height:75px;background:var(--black)"></div>
    <div class="block" style="left:441px;top:0;width:59px;height:75px;background:var(--charcoal)"></div>
    <div class="block" style="left:0;top:75px;width:441px;height:201px;background:var(--ink)"></div>
    <div class="photo" role="img" aria-label="Lake at dusk with forest shoreline" style="left:441px;top:75px;width:59px;height:201px;background:linear-gradient(180deg,#c9b79a 0%,#8a7a62 45%,#3e3a32 100%)"></div>
    <div class="hrule" style="left:0;top:75px;width:500px"></div>
    <div class="hrule" style="left:0;top:276px;width:500px"></div>
    <div class="block" style="left:0;top:276px;width:500px;height:78px;background:var(--band)"></div>
    <div class="brand-faint" style="left:112px;top:130px;font-size:82px;color:#3a3a3c">Kestrel</div>
    <div class="url" style="left:25px;top:262px">www.kestreldwellings.co.nz</div>
    <div class="contact" style="left:45px;top:320px">09 555 0142<br>sales@kestreldwellings.co.nz</div>
  </div>
  <div class="page right cover-front">
    <div class="block" style="left:0;top:0;width:500px;height:75px;background:var(--charcoal)"></div>
    <div class="cover-line">Sell the dream!</div>
    <div class="block" style="left:358px;top:75px;width:142px;height:102px;background:var(--slate)"></div>
    <div class="photo" role="img" aria-label="Timber modular cabin with lit windows on a rocky lakeshore among pines" style="left:0;top:75px;width:358px;height:201px;background:linear-gradient(160deg,#7d7566 0%,#4a4034 40%,#2b2520 75%,#171513 100%)"></div>
    <div class="block" style="left:0;top:276px;width:87px;height:78px;background:var(--band)"></div>
    <div class="vrule" style="left:358px;top:0;height:177px"></div>
    <div class="hrule" style="left:0;top:75px;width:358px"></div>
    <div class="brand-faint" style="left:398px;top:24px;font-size:22px;letter-spacing:0;color:#6a6a6c">Kestrel</div>
    <div class="url" style="left:478px;top:262px">www.kestreldwellings.co.nz</div>
    <div class="tagline" style="left:28px;top:310px">Modular<br>Architectural<br>Homes</div>
    <div class="cover-name">Kestrel</div>
  </div>
</div>

<!-- Pages 1–2 -->
<div class="label" style="left:98px;top:1123px">Page-1</div>
<div class="label" style="left:602px;top:1123px">Page-2</div>
<div class="spread" style="top:1160px">
  <div class="page left business-overview">
    <div class="block" style="left:237px;top:0;width:263px;height:277px;background:var(--white)"></div>
    <div class="block" style="left:0;top:277px;width:500px;height:77px;background:var(--band)"></div>
    <div class="block" style="left:0;top:277px;width:100px;height:77px;background:var(--band)"></div>
    <div class="vrule" style="left:100px;top:0;height:354px"></div>
    <div class="hrule" style="left:0;top:75px;width:237px"></div>
    <div class="photo" role="img" aria-label="Dark cantilevered modular home on a grassy rocky headland" style="left:100px;top:75px;width:181px;height:260px;background:linear-gradient(180deg,#e9ebec 0%,#d5d8d8 45%,#6f7d5a 70%,#4f6b33 100%)"></div>
    <div class="vertical-title">Business<br>Overview</div>
    <div class="brand-faint" style="left:410px;top:22px;font-size:22px;letter-spacing:0;color:var(--faint)">Kestrel</div>
    <div class="body-copy on-light" style="left:297px;top:87px;width:168px">
      <p>Kestrel Dwellings Developments, is an emerging New Zealand property investment company with a focus on providing unique property investment opportunities.</p>
      <p>Our expertise and capabilities in architectural modular homes provide us with a remarkable advantage in tackling the development of properties that are typically considered challenging, remote, or uniquely positioned.</p>
      <p>As a company, with 48 employees boasting a wealth of experience in handling complex architectural projects, making us well equipped to navigate the intricacies and demands of such ventures.</p>
      <p>This advantage allows us to not only execute projects efficiently but also to deliver exceptional results within condensed time frames.</p>
      <p>By capitalizing on our ability to develop difficult, remote, or one-of-a-kind properties swiftly and effectively, Kestrel Dwellings Developments offers investors a rare chance to engage in projects that promise exceptional profitability in the New Zealand property market.</p>
      <p>Our specialization in this niche sector of property development not only sets us apart from competitors, but also paves the way for lucrative investment opportunities in the New Zealand property market.</p>
    </div>
    <div class="tagline" style="left:301px;top:313px">Modular<br>Architectural<br>Homes</div>
  </div>
  <div class="page right business-origins">
    <div class="block" style="left:231px;top:0;width:269px;height:75px;background:var(--white)"></div>
    <div class="heading dark" style="left:243px;top:18px">Business<br>Origins</div>
    <div class="photo" role="img" aria-label="Lounge chairs facing a wide glass wall over the ocean and green hills" style="left:231px;top:75px;width:269px;height:204px;background:linear-gradient(180deg,#aebccb 0%,#8ea6bd 40%,#5f7787 58%,#2a2a2a 75%,#151515 100%)"></div>
    <div class="block" style="left:231px;top:279px;width:269px;height:75px;background:var(--white)"></div>
    <div class="vrule" style="left:87px;top:0;height:75px"></div>
    <div class="hrule" style="left:0;top:75px;width:231px"></div>
    <div class="body-copy on-dark" style="left:30px;top:100px;width:168px">
      <p>Kestrel Dwellings Developments was established with the goal of transforming the property investment market in New Zealand by introducing an innovative approach that centers on architectural modular designs and streamlined project timelines.</p>
      <p>Driven by our enthusiasm for architecture and real estate, we have expanded our successful business model to not only offer financial opportunities for investors but also to expand on our passion for high-end architectural design.</p>
      <p>With a wealth of experience accumulated over the past six years in the construction and the property market, we are pivoting to focus solely on our property development initiatives, presenting completed Kestrel projects to the market, in exclusive locations.</p>
      <p>These projects will boast high-quality standards, meticulous attention to detail and landscaping, and creative design elements.</p>
      <p>By introducing completed Kestrel properties into the market, we aim to reach a wider audience, catering to individuals who prefer ready-to-occupy homes over engaging in the design and construction process. This approach also simplifies the financing process for prospective buyers, as established properties are often preferred by financial lenders.</p>
    </div>
    <div class="tagline dark" style="left:248px;top:313px">Modular<br>Architectural<br>Homes</div>
    <div class="brand-faint" style="left:405px;top:302px;font-size:22px;letter-spacing:0;color:var(--faint)">Kestrel</div>
  </div>
</div>

<!-- Pages 3–4 -->
<div class="label" style="left:98px;top:1531px">Page-3</div>
<div class="label" style="left:602px;top:1531px">Page-4</div>
<div class="spread" style="top:1566px">
  <div class="page left competitive-advantage">
    <div class="photo" role="img" aria-label="Glass pavilion home with flat roof overlooking a lake at sunset" style="left:0;top:0;width:287px;height:354px;background:linear-gradient(180deg,#aeb8c2 0%,#d9c0b0 35%,#e8b98e 50%,#4a4745 65%,#3c3a38 85%,#6b5d50 100%)"></div>
    <div class="vrule" style="left:100px;top:0;height:75px;background:rgba(255,255,255,.5)"></div>
    <div class="hrule" style="left:0;top:75px;width:100px;background:rgba(255,255,255,.5)"></div>
    <div class="heading" style="left:113px;top:57px">Competitive<br>Advantage</div>
    <div class="body-copy on-dark" style="left:306px;top:104px;width:172px">
      <p>Our competitive advantage lies in the uniqueness of our property investment opportunities. Unlike traditional real estate companies, we focus on offering properties that are not only profitable but also aesthetically pleasing and unique. By catering to the tastes of architecture lovers, we set ourselves apart from the competition and attract a niche market of customers who appreciate the artistry and design of our projects.</p>
      <p>Additionally, the streamlined and condensed timelines facilitated by our modular approach provide quicker returns on investment.</p>
    </div>
    <div class="block" style="left:287px;top:276px;width:213px;height:78px;background:var(--band)"></div>
    <div class="tagline" style="left:306px;top:310px">Modular<br>Architectural<br>Homes</div>
    <div class="brand-faint" style="left:405px;top:300px;font-size:22px;letter-spacing:0;color:#5a5a5c">Kestrel</div>
  </div>
  <div class="page right financial-summary">
    <div class="block" style="left:201px;top:0;width:299px;height:75px;background:var(--white)"></div>
    <div class="heading dark" style="left:213px;top:18px">Financial<br>Summary</div>
    <div class="block" style="left:346px;top:75px;width:154px;height:279px;background:var(--white)"></div>
    <div class="block" style="left:279px;top:295px;width:221px;height:59px;background:var(--white)"></div>
    <div class="block" style="left:0;top:295px;width:279px;height:59px;background:var(--band)"></div>
    <div class="vrule" style="left:100px;top:0;height:75px"></div>
    <div class="hrule" style="left:0;top:75px;width:201px"></div>
    <div class="photo" role="img" aria-label="Black timber two-storey modular home among trees and landscaped garden" style="left:44px;top:75px;width:302px;height:220px;background:linear-gradient(180deg,#c7cdc9 0%,#6f7f64 30%,#252624 55%,#1a1a1a 70%,#8d9284 88%,#cfd2cd 100%)"></div>
    <div class="body-copy on-light" style="left:357px;top:82px;width:132px">
      <p>In terms of financial projections, with each development, we anticipate a profit of 10%-20% which will be project dependent.</p>
      <p>This growth is fueled by the increasing demand for unique property investments in New Zealand and our ability to deliver high-quality services to the market in a condensed time frame, with heavily controlled costs.</p>
      <p>With a solid business model and a dedicated team, we are confident in our ability to achieve success and establish Kestrel Dwellings Investments as a trusted name in the industry.</p>
      <p>New Zealand's property market has been experiencing steady growth over the years, making it an attractive destination for property investors. With its beautiful landscapes and strong economy, New Zealand offers a diverse range of investment opportunities for both local and international investors. The demand for quality properties in prime locations continues to rise, creating a favorable environment for property investment companies like ours that can lean on our modular benefits of being able to reach unique and remote locations.</p>
    </div>
    <div class="tagline" style="left:214px;top:316px">Modular<br>Architectural<br>Homes</div>
    <div class="brand-faint" style="left:405px;top:300px;font-size:22px;letter-spacing:0;color:var(--faint)">Kestrel</div>
  </div>
</div>

<!-- Pages 5–6 -->
<div class="label" style="left:98px;top:1932px">Page-5</div>
<div class="label" style="left:602px;top:1932px">Page-6</div>
<div class="spread" style="top:1967px">
  <div class="page left gallery">
    <div class="block" style="left:0;top:275px;width:500px;height:79px;background:var(--band)"></div>
    <div class="photo" role="img" aria-label="Interior with floor-to-ceiling glass framing green hills and a harbour" style="left:42px;top:20px;width:417px;height:301px;background:linear-gradient(180deg,#e6eaee 0%,#c3ced6 35%,#8793a0 50%,#6f8a4e 62%,#8a9a5a 75%,#b89b78 88%,#7a5e45 100%)"></div>
    <div class="vrule" style="left:100px;top:0;height:75px;background:rgba(255,255,255,.45)"></div>
    <div class="hrule" style="left:0;top:75px;width:100px;background:rgba(255,255,255,.45)"></div>
  </div>
  <div class="page right gallery">
    <div class="block" style="left:0;top:275px;width:500px;height:79px;background:var(--band)"></div>
    <div class="photo" role="img" aria-label="Long low modular home on golden coastal farmland above the sea at sunset" style="left:42px;top:20px;width:417px;height:301px;background:linear-gradient(180deg,#8a7358 0%,#b09a7c 20%,#a58d6e 35%,#5a4a32 50%,#3c3322 70%,#6d5426 85%,#8a6a2c 100%)"></div>
    <div class="vrule" style="left:64px;top:0;height:75px;background:rgba(255,255,255,.45)"></div>
    <div class="hrule" style="left:0;top:75px;width:100px;background:rgba(255,255,255,.45)"></div>
  </div>
</div>

</body>
</html>
```